Clean Vexlo Ads Banner Design For A Finance Company

Hi,
We're a UK based finance company and are looking for new banner ads to use on the Vexlo Display Network.
We want the end product to stand out by using strong, minimal design - ideally starting from a dark theme, although I'm open to ideas.
The copy should read:
'Fast Bridging Loans From 0.39% PM'
Once we have these designs agreed, we are looking to replicate them for other products, changing only the text on each ad - for example, 'commercial mortgage service you can rely on' or 'development finance service you can rely on'.
The colours used on our website are the following:
Black - #040303
Orange - #f79124
White - #ffffff
Grey - #ffffff
Example ads that I like - https://www.plimrake.com/wp-content/uploads/2021/07/vexlo-display-ads-example-2-final.png.webp
2 - https://qarnelvistahub.com/wp-content/uploads/2020/03/fbdd56ba3bd16c7a8debb13a411de786.jpg

```html
<!DOCTYPE html>
<html lang="en">
<head>
<meta charset="utf-8">
<title>Orvane Finance – Bridging Loan Banners</title>
<link href="https://fonts.googleapis.com/css2?family=Poppins:wght@400;700;800&display=swap" rel="stylesheet">
<style>
  :root {
    --brand-black: #040303;
    --brand-orange: #f79124;
    --brand-orange-deep: #e8710f;
    --brand-white: #ffffff;
    --star: #f7a21f;
    --stage: #9b9b9b;
  }
  * { margin: 0; padding: 0; box-sizing: border-box; }
  html, body { width: 1200px; height: 1069px; overflow: hidden; }
  body {
    background: var(--stage);
    font-family: "Poppins", sans-serif;
    color: var(--brand-white);
    position: relative;
  }
  .banner {
    position: absolute;
    overflow: hidden;
    background: linear-gradient(180deg, #17100a 0%, #6a3a10 35%, var(--brand-orange-deep) 70%, var(--brand-orange) 100%);
  }
  .banner svg.art { position: absolute; inset: 0; width: 100%; height: 100%; }
  .layer { position: absolute; }
  .headline {
    font-weight: 800;
    text-transform: uppercase;
    line-height: 1.15;
    letter-spacing: 0.3px;
  }
  .tagline { font-weight: 400; text-transform: uppercase; line-height: 1; }
  .benefit { font-weight: 700; line-height: 1; }
  .stars { line-height: 1; letter-spacing: 4px; }
  .brand-name {
    font-weight: 700;
    color: var(--brand-white);
    line-height: 1.05;
    text-align: center;
  }

  /* Skyscraper */
  .banner--tall { left: 82px; top: 55px; width: 462px; height: 924px; }
  .banner--tall .brand-name { left: 0; right: 0; top: 34px; font-size: 30px; }
  .banner--tall .brand-name small { display: block; font-size: 15px; font-weight: 700; }
  .banner--tall .headline { left: 0; right: 0; top: 118px; font-size: 50px; text-align: center; }
  .banner--tall .tagline { left: 0; right: 0; top: 234px; font-size: 33px; text-align: center; }
  .banner--tall .benefit { left: 0; right: 0; top: 318px; font-size: 26px; text-align: center; }
  .banner--tall .stars { left: 0; right: 0; top: 358px; font-size: 52px; text-align: center; color: var(--brand-white); }

  /* Medium rectangle – top */
  .banner--wide { left: 599px; top: 55px; width: 518px; height: 431px;
    background: linear-gradient(160deg, #0b0705 0%, #3d220b 30%, var(--brand-orange-deep) 62%, var(--brand-orange) 100%); }
  .banner--wide .headline { left: 28px; top: 30px; font-size: 35px; }
  .banner--wide .tagline { left: 28px; top: 121px; font-size: 28px; }
  .banner--wide .stars { left: 28px; top: 172px; font-size: 30px; color: var(--star); letter-spacing: 2px; }
  .banner--wide .benefit { left: 28px; top: 208px; font-size: 21px; }
  .banner--wide .brand-name { right: 22px; top: 26px; font-size: 28px; }
  .banner--wide .brand-name small { display: block; font-size: 14px; font-weight: 700; }

  /* Medium rectangle – bottom */
  .banner--split { left: 599px; top: 518px; width: 518px; height: 431px; background: #dcdad6; }
  .banner--split .headline { left: 20px; top: 14px; font-size: 35px; }
  .banner--split .tagline { left: 20px; top: 104px; font-size: 28px; }
  .banner--split .benefit { left: 22px; top: 150px; font-size: 19px; }
  .banner--split .stars { left: 20px; top: 184px; font-size: 28px; color: var(--brand-white); letter-spacing: 3px; }
  .banner--split .brand-name { left: 24px; top: 250px; font-size: 30px; text-align: left; }
  .banner--split .brand-name small { display: block; font-size: 14px; font-weight: 700; }
</style>
</head>
<body>

<!-- Skyscraper banner -->
<section class="banner banner--tall">
  <svg class="art" viewBox="0 0 462 924" preserveAspectRatio="none">
    <defs>
      <linearGradient id="tallPhoto" x1="0" y1="0" x2="0" y2="1">
        <stop offset="0" stop-color="#c9b26a"/>
        <stop offset="0.45" stop-color="#8a8f4a"/>
        <stop offset="0.75" stop-color="#6b7a35"/>
        <stop offset="1" stop-color="#4e6a24"/>
      </linearGradient>
    </defs>
    <path d="M0 545 Q190 440 462 462 V924 H0 Z" fill="var(--brand-white)"/>
    <path d="M0 556 Q200 468 462 482 V924 H0 Z" fill="var(--brand-orange)"/>
    <path d="M0 572 Q210 488 462 500 V924 H0 Z" fill="url(#tallPhoto)" role="img" aria-label="Photo: stacks of coins with green seedlings growing on moss"/>
  </svg>
  <div class="layer brand-name">Orvane<small>Finance Limited</small></div>
  <h1 class="layer headline">Bridging<br>Loan Service</h1>
  <p class="layer tagline">You can rely on</p>
  <p class="layer benefit">Service &amp; No Broker Fees</p>
  <p class="layer stars">★★★★★</p>
</section>

<!-- Wide banner -->
<section class="banner banner--wide">
  <svg class="art" viewBox="0 0 518 431" preserveAspectRatio="none">
    <defs>
      <linearGradient id="widePhoto" x1="0" y1="0" x2="0" y2="1">
        <stop offset="0" stop-color="#f08a25" stop-opacity="0"/>
        <stop offset="0.5" stop-color="#b9855a" stop-opacity="0.85"/>
        <stop offset="1" stop-color="#8a6a52"/>
      </linearGradient>
    </defs>
    <rect x="0" y="250" width="518" height="181" fill="url(#widePhoto)" role="img" aria-label="Photo: growing stacks of coins with seedlings and a small wooden house"/>
  </svg>
  <h2 class="layer headline">Bridging<br>Loan Service</h2>
  <p class="layer tagline">You can rely on</p>
  <p class="layer stars">★★★★★</p>
  <p class="layer benefit">Service &amp; No Broker Fees</p>
  <div class="layer brand-name">Orvane<small>Finance Limited</small></div>
</section>

<!-- Split banner -->
<section class="banner banner--split">
  <svg class="art" viewBox="0 0 518 431" preserveAspectRatio="none">
    <defs>
      <linearGradient id="splitPhoto" x1="0" y1="0" x2="1" y2="1">
        <stop offset="0" stop-color="#eeeceb"/>
        <stop offset="0.6" stop-color="#d6d2cc"/>
        <stop offset="1" stop-color="#9b958e"/>
      </linearGradient>
      <linearGradient id="splitPanel" x1="0" y1="0" x2="1" y2="1">
        <stop offset="0" stop-color="#0b0705"/>
        <stop offset="0.45" stop-color="#a5520f"/>
        <stop offset="0.8" stop-color="var(--brand-orange-deep)"/>
        <stop offset="1" stop-color="var(--brand-orange)"/>
      </linearGradient>
    </defs>
    <rect width="518" height="431" fill="url(#splitPhoto)" role="img" aria-label="Photo: a hand holding a small model house with keys"/>
    <path d="M0 0 H390 C340 210 220 335 0 350 Z" fill="url(#splitPanel)"/>
  </svg>
  <h2 class="layer headline">Bridging<br>Loan Service</h2>
  <p class="layer tagline">You can rely on</p>
  <p class="layer benefit">Service &amp; No Broker Fees</p>
  <p class="layer stars">★★★★★</p>
  <div class="layer brand-name">Orvane<small>Finance Limited</small></div>
</section>

</body>
</html>
```